Corporate Business Card

Very professional, Modern, Not to busy, include phone address email, website
(253) 617-4930, 18761 52nd Avenue S, Kent, WA 98047, martin@plumlinegroup.com, varkoworks.com

Target Market(s)

Manufacturing

Industry/Entity Type

Aero, machining, manufacturing, Off road racing

Contact Information for Business Card

Phone, address email, website

```html
<!DOCTYPE html>
<html lang="en">
<head>
<meta charset="utf-8">
<title>Varko Works – Business Card</title>
<link rel="stylesheet" href="https://fonts.googleapis.com/css2?family=Didact+Gothic&display=swap">
<style>
  :root {
    --navy: #17356b;
    --red: #d0232b;
    --white: #ffffff;
    --backdrop: #ecebec;
    --pattern: #dfe3eb;
  }
  * { margin: 0; padding: 0; box-sizing: border-box; }
  html, body { width: 1200px; height: 1200px; overflow: hidden; }
  body {
    background: var(--backdrop);
    font-family: "Didact Gothic", "Century Gothic", sans-serif;
    position: relative;
  }
  .card {
    position: absolute;
    left: 210px;
    width: 780px;
    height: 446px;
    overflow: hidden;
    box-shadow: 0 6px 14px rgba(0,0,0,0.18);
  }
  .card--front { top: 100px; background: var(--navy); }
  .card--back { top: 660px; background: var(--white); }
  .card__bg { position: absolute; inset: 0; width: 100%; height: 100%; }

  .brand-name {
    position: absolute;
    white-space: nowrap;
    line-height: 1;
    letter-spacing: 1px;
  }
  .card--front .brand-name {
    left: 310px;
    top: 172px;
    width: 420px;
    text-align: center;
    font-size: 62px;
    color: var(--white);
  }
  .card--back .brand-name {
    left: 40px;
    top: 56px;
    font-size: 40px;
    color: var(--navy);
  }

  .contact-icons {
    position: absolute;
    left: 42px;
    top: 244px;
    width: 200px;
    height: 36px;
  }
  .contact-list {
    position: absolute;
    left: 44px;
    top: 296px;
    list-style: none;
    color: var(--navy);
    font-size: 17.5px;
    line-height: 27.5px;
    letter-spacing: 0.3px;
  }
</style>
</head>
<body>

<section class="card card--front" aria-label="Card front">
  <svg class="card__bg" viewBox="0 0 780 446" preserveAspectRatio="none" aria-hidden="true">
    <polygon points="0,0 309,0 68,446 0,446" fill="var(--red)"/>
  </svg>
  <p class="brand-name">Varko Works</p>
</section>

<section class="card card--back" aria-label="Card back">
  <svg class="card__bg" viewBox="0 0 780 446" preserveAspectRatio="none">
    <polygon role="img" aria-label="Faint repeated brand name pattern" points="582,0 780,0 780,446 385,446" fill="var(--pattern)" opacity="0.7"/>
  </svg>
  <p class="brand-name">Varko Works</p>

  <svg class="contact-icons" viewBox="0 0 200 36" aria-hidden="true">
    <line x1="16" y1="18" x2="180" y2="18" stroke="var(--red)" stroke-width="1.6"/>
    <g fill="var(--red)">
      <circle cx="16" cy="18" r="16"/>
      <circle cx="70" cy="18" r="16"/>
      <circle cx="124" cy="18" r="16"/>
      <circle cx="178" cy="18" r="16"/>
    </g>
    <g fill="none" stroke="var(--white)" stroke-width="1.6" stroke-linecap="round" stroke-linejoin="round">
      <!-- phone -->
      <path d="M10 11 q-2 2 0 6 q3 6 9 8 q3 1 4-1 l-3-3 -2 1 q-3-1-5-5 l1-2 z"/>
      <path d="M17 10 a6 6 0 0 1 5 5 M17 7 a9 9 0 0 1 8 8"/>
      <!-- envelope -->
      <rect x="62" y="12" width="16" height="12" rx="1"/>
      <path d="M62 13 l8 6 8-6 M62 24 l6-5 M78 24 l-6-5"/>
      <!-- pin -->
      <path d="M124 26 q-6-6-6-10 a6 6 0 0 1 12 0 q0 4-6 10 z"/>
      <circle cx="124" cy="16" r="2"/>
      <!-- globe -->
      <circle cx="178" cy="18" r="8"/>
      <ellipse cx="178" cy="18" rx="3.5" ry="8"/>
      <path d="M170 18 h16 M171.5 14 h13 M171.5 22 h13"/>
    </g>
  </svg>

  <ul class="contact-list">
    <li>(253) 617-4930, 18761</li>
    <li>varkoworks.com</li>
    <li>52nd Avenue S, Kent, WA 98047</li>
    <li>martin@plumlinegroup.com</li>
  </ul>
</section>

</body>
</html>
```